Card Design for my dog training business Brightpaw Obedience

Need a business card design for my dog training business with my new logo. Want the card to come off professional yet fun. Want it to be very eye catchy as well. I normally have these at vet clinics, pet stores, and groomers. so need it to look better than my competitors.
Target Market(s)
dog owners
Industry/Entity Type
Dog Training
Contact Information for Business Card
needs logo, my name and info
Font styles to use
Serif
Colors
0255a3
ffffff
ec1f27
000000
333333
fbfbfb
Requirements
Must have
- Brightpaw Obedience
- Felix Orland
- 415 903 2276
- info@brightpawobedience.example
- www.brightpawobedience.example

```html
<!DOCTYPE html>
<html lang="en">
<head>
<meta charset="utf-8">
<title>Brightpaw Obedience – Business Card</title>
<link rel="stylesheet" href="https://fonts.googleapis.com/css2?family=Roboto:wght@400;500;700&family=EB+Garamond:ital@1&display=swap">
<style>
  :root {
    --page: #fbfbfb;
    --card: #ffffff;
    --ink: #000000;
    --ink-soft: #333333;
    --rule: #555555;
    --back: #231f20;
    --back-text: #ffffff;
  }
  * { box-sizing: border-box; margin: 0; padding: 0; }
  html, body { width: 1125px; height: 1200px; overflow: hidden; }
  body {
    background: var(--page);
    font-family: "Roboto", Arial, sans-serif;
    position: relative;
  }
  .card {
    position: absolute;
    left: 171px;
    width: 826px;
    box-shadow: 0 2px 6px rgba(0,0,0,0.25);
  }
  .card-front {
    top: 106px;
    height: 472px;
    background: var(--card);
    border-bottom: 13px solid var(--back);
  }
  .brand {
    position: absolute;
    right: 60px;
    top: 130px;
    display: flex;
    align-items: center;
    gap: 10px;
    font-weight: 500;
    font-size: 20px;
    color: var(--ink);
    letter-spacing: 0.5px;
  }
  .brand-mark { width: 16px; height: 16px; background: var(--ink); }
  .holder-name {
    position: absolute;
    left: 41px;
    top: 298px;
    font-weight: 700;
    font-size: 29px;
    color: var(--ink-soft);
  }
  .divider {
    position: absolute;
    left: 41px;
    right: 41px;
    top: 352px;
    border-top: 1px solid var(--rule);
  }
  .contact {
    position: absolute;
    left: 41px;
    top: 376px;
    list-style: none;
    font-size: 19px;
    color: var(--ink-soft);
    line-height: 27px;
  }
  .contact li { display: flex; align-items: center; gap: 11px; }
  .contact svg { width: 18px; height: 18px; fill: var(--ink); }
  .website {
    position: absolute;
    right: 43px;
    top: 403px;
    font-size: 19px;
    color: var(--ink-soft);
    line-height: 27px;
  }
  .card-back {
    top: 639px;
    height: 470px;
    background: var(--back);
    color: var(--back-text);
  }
  .back-brand {
    position: absolute;
    left: 0; right: 0;
    top: 196px;
    display: flex;
    justify-content: center;
    align-items: center;
    gap: 16px;
    font-weight: 500;
    font-size: 44px;
    letter-spacing: 1px;
  }
  .back-brand .brand-mark { width: 30px; height: 30px; background: var(--back-text); }
  .tagline {
    position: absolute;
    left: 0; right: 0;
    top: 402px;
    text-align: center;
    font-family: "EB Garamond", Georgia, serif;
    font-style: italic;
    font-size: 24px;
  }
</style>
</head>
<body>
  <section class="card card-front">
    <div class="brand"><span class="brand-mark"></span>Brightpaw Obedience</div>
    <h1 class="holder-name">Felix Orland</h1>
    <div class="divider"></div>
    <ul class="contact">
      <li>
        <svg viewBox="0 0 24 24" aria-hidden="true"><path d="M6.6 10.8a15.1 15.1 0 0 0 6.6 6.6l2.2-2.2a1 1 0 0 1 1-.25 11.4 11.4 0 0 0 3.6.57 1 1 0 0 1 1 1V20a1 1 0 0 1-1 1A17 17 0 0 1 3 4a1 1 0 0 1 1-1h3.5a1 1 0 0 1 1 1c0 1.25.2 2.45.57 3.57a1 1 0 0 1-.25 1z"/></svg>
        415 903 2276
      </li>
      <li>
        <svg viewBox="0 0 24 24" aria-hidden="true"><path d="M3 6h18v12H3z M4.5 7.5v.4l7.5 5 7.5-5v-.4z" fill-rule="evenodd"/></svg>
        info@brightpawobedience.example
      </li>
    </ul>
    <div class="website">www.brightpawobedience.example</div>
  </section>

  <section class="card card-back">
    <div class="back-brand"><span class="brand-mark"></span>Brightpaw Obedience</div>
    <p class="tagline">“Building good habits in every dog, one at a time.”</p>
  </section>
</body>
</html>
```